Web and Logo Design for eCommerce site

We're launching a sister brand and require a full design for the site.

The site must have an established feel and appeal to corporate and institutional buyers.
Updates

Just a note about the wireframe design:

The Search & Rescue / Coast Guard / NVDK, etc. in the header area aren't buttons or menu items, but rather just info (along the lines of a tagline).  Sort of a "who we serve" sort of thing.

Worth noting is that it's specifically geared towards LARGE BUYERS.  For example, a police force buying 200 headlamps and 85 pairs of gloves.  So they'll register + sign in and then add a bunch of items to a RFQ.

Aim for a professional, masculine design.

Target Market(s)

We will be selling outdoor gear to the military, law enforcement, fire and rescue and first responders.

Requirements
Must have
• We require:
- Logo (vector based)

Site:
- template page
* main site template, re-skinned version of our current site
* horizontal drop-down menu
- product listings page
* thumbnail view of products
- product details page
* including elements such as product image, color/size selector, descriptions and specs (again, based loosely on our current website)
- account management page
* illustrating basic data entry styles for text box, buttons, grid, etc.

The site needs to be given a responsive design, so 2 versions of each design should be presented for desktop + mobile views.

Additional funds are available if the designer is able to fully implement the designs into a responsive framework such as bootstrap.

Nice to have
• Clean, professional design similar to:

http://military.trailvexagear.com/gov/accessories/gloves.html

http://leaf.ombrivo.com/ProductFind.aspx?language=EN&category=Hardshell&subcat=Waterproof_Jackets

```html
<!DOCTYPE html>
<html lang="en">
<head>
<meta charset="utf-8">
<title>Northcadre – Helmets</title>
<link href="https://fonts.googleapis.com/css2?family=Open+Sans:wght@400;600;700&family=Special+Elite&display=swap" rel="stylesheet">
<style>
:root{
  --ink:#1f2326;
  --dark:#17120d;
  --olive:#9aa34a;
  --brand:#3d4a2a;
  --btn:#5d6233;
  --btn-text:#f4f1e4;
  --panel:#f1f1f1;
  --line:#dcdcdc;
  --sky:#d5e2e2;
  --text:#2a2a2a;
  --price:#5d6233;
}
*{box-sizing:border-box;margin:0;padding:0}
html,body{width:1116px;height:1200px;overflow:hidden}
body{position:relative;background:#fff;font-family:"Open Sans",Arial,sans-serif;color:var(--text)}
.abs{position:absolute}
.topbar{left:0;top:0;width:1116px;height:32px;background:var(--ink)}
.served{left:102px;top:9px;display:flex;font-size:10px;color:#e6e6e6}
.served span+span::before{content:"|";margin:0 11px;color:#bbb}
.social{right:24px;top:6px;display:flex;gap:6px}
.social i{display:block;width:20px;height:20px;border-radius:50%;background:#fff}
.header{left:0;top:32px;width:1116px;height:78px;background:#fff}
.brand{left:104px;top:10px;display:flex;align-items:center;gap:10px}
.brand .mark{width:46px;height:46px;background:var(--brand)}
.brand .name{font-size:30px;font-weight:700;color:var(--brand)}
.brand-sub{left:160px;top:56px;font-size:10px;color:var(--brand);letter-spacing:1px}
.contact{right:24px;top:30px;display:flex;align-items:center;gap:8px;font-size:13px;color:#666}
.contact svg{display:block}
.sky{left:0;top:110px;width:1116px;height:457px;background:var(--sky)}
.nav{left:102px;top:110px;width:912px;height:39px;background:var(--ink);display:flex;align-items:center;padding-left:20px;font-size:13.5px}
.nav a{color:var(--olive);text-decoration:none;margin-right:27px}
.nav a.active{color:#fff}
.nav .search{position:absolute;right:12px;top:7px;width:25px;height:24px;background:var(--olive)}
.panel{left:102px;top:153px;width:912px;height:750px;background:var(--panel);border:1px solid var(--line);border-radius:3px}
.crumbs{left:114px;top:166px;width:890px;height:34px;background:#fff;border-radius:3px;padding:9px 12px;font-size:12px}
.crumbs a{color:var(--text)}
.side{left:119px}
.side h2{font-size:17px;font-weight:600;color:#222;margin-bottom:6px}
.side h3{font-size:13.5px;font-weight:400;color:#222;margin-bottom:6px}
.side li{list-style:none;font-size:11.5px;line-height:16px;color:#555}
.banner{left:332px;top:209px;width:672px;height:161px;background:linear-gradient(90deg,#220707 0%,#3a0a05 45%,#a8380c 68%,#3b2415 85%,#1a1410 100%)}
.banner-title{left:370px;top:264px;font-size:40px;color:#ece4dc;font-family:"Special Elite","Courier New",monospace}
.listing-title{left:332px;top:412px;font-size:17px;font-weight:600;color:#222}
.sort{left:806px;top:439px;display:flex;align-items:center;gap:8px;font-size:12px}
.sort .select{width:145px;height:18px;background:#fff;border:1px solid #ccc;font-size:10.5px;color:#888;padding:1px 4px;position:relative}
.sort .select::after{content:"";position:absolute;right:0;top:0;width:16px;height:16px;border-left:1px solid #ccc;background:linear-gradient(#fff,#eee)}
.viewing{left:332px;top:461px;width:672px;height:32px;background:#fff;font-size:12px;padding:8px 9px}
.grid{left:332px;top:514px;display:grid;grid-template-columns:repeat(5,128px);column-gap:7px;row-gap:11px}
.card{height:175px;background:#fafafa;border:1px solid #e6e6e6;border-radius:3px;text-align:center;padding-top:18px}
.card .thumb{width:62px;height:66px;margin:0 auto;border-radius:30px 30px 10px 10px}
.card .name{font-size:13px;margin-top:16px;color:#222;white-space:nowrap}
.card .price{font-size:13px;font-weight:600;color:var(--price);margin-top:8px}
.card .add{display:inline-block;margin-top:6px;background:var(--btn);color:var(--btn-text);font-size:12px;padding:1px 4px}
.footer{left:0;top:929px;width:1116px;height:271px;background:var(--dark);color:#ddd}
.fcol{top:44px}
.fcol h4{font-size:16px;font-weight:600;color:#fff;margin-bottom:10px}
.fcol li{list-style:none;font-size:12.5px;line-height:14.5px;color:#ddd}
.fcol p{font-size:12px;line-height:19px;color:#aaa;width:250px}
.signup{left:422px;top:139px;display:flex}
.signup .field{width:178px;height:35px;background:#fff;color:#999;font-size:12px;padding:10px}
.signup .go{width:57px;height:35px;background:#d8d8d8;color:#333;font-size:14px;padding:8px 10px}
.map{left:738px;top:63px;width:239px;height:154px;background:linear-gradient(135deg,#f0eee6,#e7e2cc 50%,#f2eedd)}
.copy{left:0;top:240px;width:1116px;text-align:center;font-size:12.5px;color:#fff}
</style>
</head>
<body>
<div class="abs topbar"></div>
<div class="abs served"><span>SEARCH &amp;RECUE</span><span>COAST GUARD</span><span>NVDK</span><span>FIRE</span><span>MILIATRY</span><span>LAW ENFORCEMENT</span></div>
<div class="abs social"><i></i><i></i><i></i><i></i></div>

<div class="abs header">
  <div class="abs brand"><span class="mark"></span><span class="name">Northcadre</span></div>
  <div class="abs brand-sub">NORTHERN TACTICAL SUPPLY</div>
  <div class="abs contact">
    <svg width="18" height="18" viewBox="0 0 24 24"><path d="M6.6 10.8a15 15 0 0 0 6.6 6.6l2.2-2.2c.3-.3.7-.4 1-.2 1.1.4 2.3.6 3.6.6.6 0 1 .4 1 1V20c0 .6-.4 1-1 1A17 17 0 0 1 3 4c0-.6.4-1 1-1h3.5c.6 0 1 .4 1 1 0 1.3.2 2.5.6 3.6.1.3 0 .7-.2 1z" fill="#999"/></svg>
    <span>Call (+) 0800.555.019</span>
    <svg width="18" height="16" viewBox="0 0 24 20"><path d="M2 7h20l-2.5 11h-15zM7 7l4-6M17 7l-4-6" fill="none" stroke="#888" stroke-width="2"/></svg>
    <span>(0 item) - $0.00 &nbsp;▾</span>
  </div>
</div>

<div class="abs sky"></div>
<nav class="abs nav">
  <a class="active">RESCUE GEAR</a><a>FOOTWEAR</a><a>CLOTHING</a><a>TENTS MATS SLEEPING BAGS</a><a>CAMPING GEAR</a><a>SNOW SPORTS</a><a>BRAND'S</a>
  <span class="search"><svg width="25" height="24" viewBox="0 0 25 24"><circle cx="11" cy="10.5" r="5" fill="none" stroke="#fff" stroke-width="2"/><path d="M14.5 14l4 4" stroke="#fff" stroke-width="2.4"/></svg></span>
</nav>

<div class="abs panel"></div>
<div class="abs crumbs"><a>Rescue Gear</a> &nbsp;&gt;&nbsp; <a>Helmet</a></div>

<aside class="abs side" style="top:221px">
  <h2>Rescue Gear (602)</h2>
  <ul><li>Lorem Lipsum</li><li>Dummy text dolar</li><li>Sit amet</li><li>Lorem Lipsum</li><li>Site amet</li><li>Dummy text dolar</li><li>Lorem Lipsum</li><li>Dummy text dolar</li><li>Sit amet</li><li>Lorem Lipsum</li><li>Site amet</li><li>Dummy text dolar</li></ul>
</aside>
<aside class="abs side" style="top:471px">
  <h3>Filter by Manufacture</h3>
  <ul><li>Lorem Lipsum</li><li>Dummy text dolar</li><li>Sit amet</li><li>Lorem Lipsum</li><li>Site amet</li><li>Dummy text dolar</li></ul>
</aside>

<div class="abs banner" role="img" aria-label="Firefighter in helmet beside flames"></div>
<div class="abs banner-title">Helmets</div>

<h1 class="abs listing-title">Helmets -19 Products</h1>
<div class="abs sort">Sort By <span class="select">Relevance</span></div>
<div class="abs viewing">Viewing Page: 1 of 1</div>

<div class="abs grid">
  <div class="card"><div class="thumb" role="img" aria-label="Red rescue helmet" style="background:#e0442a"></div><div class="name">Ridge Helmet</div><div class="price">Price: $9.99</div><span class="add">Add To Cart</span></div>
  <div class="card"><div class="thumb" role="img" aria-label="Yellow rescue helmet" style="background:#e9ea3a"></div><div class="name">Summit Helmet</div><div class="price">Price: $9.99</div><span class="add">Add To Cart</span></div>
  <div class="card"><div class="thumb" role="img" aria-label="Lime rescue helmet" style="background:#a6e21c"></div><div class="name">Vector Helmet</div><div class="price">Price: $9.99</div><span class="add">Add To Cart</span></div>
  <div class="card"><div class="thumb" role="img" aria-label="Navy rescue helmet" style="background:#3b4150"></div><div class="name">Harbor Helmet</div><div class="price">Price: $9.99</div><span class="add">Add To Cart</span></div>
  <div class="card"><div class="thumb" role="img" aria-label="Orange rescue helmet" style="background:#f5822a"></div><div class="name">Cascade Helmet</div><div class="price">Price: $9.99</div><span class="add">Add To Cart</span></div>
  <div class="card"><div class="thumb" role="img" aria-label="Red rescue helmet" style="background:#d8342c"></div><div class="name">Ridge Helmet</div><div class="price">Price: $9.99</div><span class="add">Add To Cart</span></div>
  <div class="card"><div class="thumb" role="img" aria-label="Lime rescue helmet" style="background:#a6e21c"></div><div class="name">Summit Helmet</div><div class="price">Price: $9.99</div><span class="add">Add To Cart</span></div>
  <div class="card"><div class="thumb" role="img" aria-label="Orange rescue helmet" style="background:#f5822a"></div><div class="name">Vector Helmet</div><div class="price">Price: $9.99</div><span class="add">Add To Cart</span></div>
  <div class="card"><div class="thumb" role="img" aria-label="Navy rescue helmet" style="background:#3b4150"></div><div class="name">Harbor Helmet</div><div class="price">Price: $9.99</div><span class="add">Add To Cart</span></div>
  <div class="card"><div class="thumb" role="img" aria-label="Yellow rescue helmet" style="background:#e9ea3a"></div><div class="name">Cascade Helmet</div><div class="price">Price: $9.99</div><span class="add">Add To Cart</span></div>
</div>

<footer class="abs footer">
  <div class="abs fcol" style="left:114px"><h4>Navigation</h4><ul><li>Rescue Gear</li><li>Footwear</li><li>Clothing</li><li>Tents Mats</li><li>Sleeping Bags</li><li>Camping Gear</li><li>Snow Sports</li><li>Brands</li></ul></div>
  <div class="abs fcol" style="left:272px"><h4>Products</h4><ul><li>Rescue Gear</li><li>Footwear</li><li>Clothing</li><li>Tents Mats</li><li>Sleeping Bags</li><li>Camping Gear</li><li>Snow Sports</li><li>Brands</li></ul></div>
  <div class="abs fcol" style="left:421px"><h4>Get informed for our Special offers</h4><p>Get the best and most interesting discount offers via email.</p></div>
  <div class="abs signup"><span class="field">you@example.com</span><span class="go">Enter</span></div>
  <div class="abs fcol" style="left:745px;top:38px"><h4>Map</h4></div>
  <div class="abs map" role="img" aria-label="Street map showing the store location"></div>
  <div class="abs copy">CopyRight © 2014 NORTHCADRE All Received</div>
</footer>
</body>
</html>
```